Wealth Education Business Needs Sharp Business Card Design

We need a business card design for a recently launched investor education business called Harbor Crest.

The final design should promote security, empowerment, self improvement and financial gain. The card will ideally promote the stature of the business.

For more information and colours please visit harborcrest.com.au

Target Market(s)

Corporate executives and high net worth individuals

Industry/Entity Type

Education

Contact Information for Business Card

```html
<!DOCTYPE html>
<html lang="en">
<head>
<meta charset="utf-8">
<title>Harbor Crest Business Card</title>
<link rel="stylesheet" href="https://fonts.googleapis.com/css2?family=Michroma&display=swap">
<style>
  :root {
    --backdrop: #8b8e8f;
    --card: #ffffff;
    --charcoal: #3f3d3e;
    --ink: #2b2a2b;
    --accent-blue: #1f9ad6;
    --accent-teal: #1a8c8a;
    --muted: #e2e2e2;
  }
  * { margin: 0; padding: 0; box-sizing: border-box; }
  html, body {
    width: 1200px; height: 771px; overflow: hidden;
    background: var(--backdrop);
    font-family: "Michroma", sans-serif;
  }
  .sheet { position: relative; width: 1200px; height: 771px; }
  .card {
    position: absolute; top: 231px;
    width: 540px; height: 309px;
    background: var(--card);
    overflow: hidden;
    box-shadow: 0 6px 18px rgba(0,0,0,.25);
  }
  .card--front { left: 40px; }
  .card--back { left: 620px; }

  .brand {
    display: flex; align-items: center; gap: 14px;
    color: var(--ink);
  }
  .brand__mark {
    width: 26px; height: 26px; border-radius: 50%;
    background: var(--accent-teal);
  }
  .brand__name {
    font-size: 27px; letter-spacing: 4px; text-transform: uppercase;
  }
  .card--front .brand {
    position: absolute; left: 50%; top: 50%;
    transform: translate(-50%, -50%);
  }

  .card__band { position: absolute; inset: 0; }
  .card--back .brand {
    position: absolute; left: 40px; top: 44px;
  }
  .card--back .brand__name { font-size: 22px; letter-spacing: 3px; }

  .contact {
    position: absolute; left: 30px; top: 150px;
    list-style: none; color: var(--muted);
    font-size: 8.5px; letter-spacing: .6px; line-height: 17px;
  }
  .contact li { display: flex; align-items: center; gap: 8px; }
  .contact__icon { width: 11px; height: 11px; flex: none; }

  .holder {
    position: absolute; right: 28px; bottom: 26px;
    text-align: right; color: #ffffff;
  }
  .holder__name { font-size: 12px; letter-spacing: 2px; }
  .holder__role { font-size: 8px; letter-spacing: 2px; color: var(--muted); margin-top: 4px; }
</style>
</head>
<body>
<main class="sheet">
  <section class="card card--front" aria-label="Card front">
    <div class="brand">
      <span class="brand__mark"></span>
      <span class="brand__name">Harbor Crest</span>
    </div>
  </section>

  <section class="card card--back" aria-label="Card back">
    <svg class="card__band" viewBox="0 0 540 309" width="540" height="309" aria-hidden="true">
      <path d="M0,128 C160,108 340,148 540,214 L540,309 L0,309 Z" fill="var(--charcoal)"/>
      <path d="M0,118 C170,94 350,134 540,202" fill="none" stroke="var(--accent-blue)" stroke-width="7"/>
    </svg>

    <div class="brand">
      <span class="brand__mark"></span>
      <span class="brand__name">Harbor Crest</span>
    </div>

    <ul class="contact">
      <li><svg class="contact__icon" viewBox="0 0 12 12"><path d="M6 1a3.5 3.5 0 0 0-3.5 3.5C2.5 7.5 6 11 6 11s3.5-3.5 3.5-6.5A3.5 3.5 0 0 0 6 1z" fill="#e2e2e2"/><circle cx="6" cy="4.5" r="1.2" fill="#3f3d3e"/></svg>Suite 14, Quay House</li>
      <li><span class="contact__icon"></span>Sydney NSW 2000</li>
      <li><svg class="contact__icon" viewBox="0 0 12 12"><circle cx="6" cy="6" r="5.5" fill="#e2e2e2"/><path d="M4 3.2l1 1.6-.6.7c.5 1 1.1 1.6 2.1 2.1l.7-.6 1.6 1-.6 1.2C5.8 9 3 6.2 2.8 3.8z" fill="#3f3d3e"/></svg>02 9000 4172</li>
      <li><svg class="contact__icon" viewBox="0 0 12 12"><circle cx="6" cy="6" r="5.5" fill="#e2e2e2"/><rect x="3" y="4" width="6" height="4.5" fill="#3f3d3e"/></svg>02 9000 4173</li>
      <li><svg class="contact__icon" viewBox="0 0 12 12"><circle cx="6" cy="6" r="5.5" fill="#e2e2e2"/><rect x="4.2" y="2.8" width="3.6" height="6.4" rx=".6" fill="#3f3d3e"/></svg>0400 118 205</li>
      <li><svg class="contact__icon" viewBox="0 0 12 12"><circle cx="6" cy="6" r="5.5" fill="#e2e2e2"/><rect x="3" y="3.8" width="6" height="4.4" fill="none" stroke="#3f3d3e" stroke-width=".9"/><path d="M3 3.8l3 2.4 3-2.4" fill="none" stroke="#3f3d3e" stroke-width=".9"/></svg>daniel@harborcrest.com.au</li>
      <li><svg class="contact__icon" viewBox="0 0 12 12"><circle cx="6" cy="6" r="5.5" fill="#e2e2e2"/><circle cx="6" cy="6" r="3" fill="none" stroke="#3f3d3e" stroke-width=".9"/><path d="M3 6h6M6 3v6" stroke="#3f3d3e" stroke-width=".7"/></svg>www.harborcrest.com.au</li>
    </ul>

    <div class="holder">
      <p class="holder__name">Daniel Reeve</p>
      <p class="holder__role">OWNER / C.E.O</p>
    </div>
  </section>
</main>
</body>
</html>
```